4th Generation Family Business Needs a New Card Design!

We are a family owned 4th Generation company. We are based in the Sydney, Australia area and we are desperately in need of a more modern and classy card. We are monumental masons who design, supply & erect lasting memorials throughout cemeteries in Sydney. Our customers are normally in a period of grieving. I have attached logo files that will need to be implemented on the card. Company was established 1935. Australian Owned and Operated. Card needs to be designed to PIXO.com specification.

Target Market(s)

Our target market is based upon people that a grieving for family members that have passed away. We also deal with alot of companies that own and operate cemeteries.

Industry/Entity Type

Business

Contact Information for Business Card

Simon Harcourt, Operations Manager, 0417293086, simon@harcourtmemorials.com.au
Lewis Harcourt, Director, 0491630572, lewis@harcourtmemorials.com.au
Phone # 02 9561 3048
Website: www.harcourtmemorials.com.au
Address: Suite 17, 8 Palfrey Lane, West Carlow, Sydney NSW 2156

Font styles to use
Serif
Decorative
Script

Requirements
Must have
• Would like to see the logo nicely implemented with a modern design. Embossed lettering would be a nice additive.

```html
<!DOCTYPE html>
<html lang="en">
<head>
<meta charset="utf-8">
<title>Harcourt Memorials — Business Cards</title>
<link rel="stylesheet" href="https://fonts.googleapis.com/css2?family=Open+Sans:wght@400;600;700&display=swap">
<style>
  :root {
    --gold: #ebbd2f;
    --ink: #231f20;
    --paper: #ffffff;
    --backdrop: #ece9e4;
    --shadow: rgba(0, 0, 0, 0.18);
  }
  * { box-sizing: border-box; margin: 0; padding: 0; }
  html, body { width: 1200px; height: 900px; overflow: hidden; }
  body {
    background: var(--backdrop);
    font-family: "Open Sans", Arial, sans-serif;
    position: relative;
  }
  .card {
    position: absolute;
    top: 285px;
    width: 540px;
    height: 330px;
    overflow: hidden;
    box-shadow: 0 10px 28px var(--shadow);
    display: flex;
    flex-direction: column;
  }
  .card--company { left: 40px; }
  .card--staff { left: 620px; }

  .wordmark {
    font-family: "Open Sans", Arial, sans-serif;
    font-weight: 600;
    text-transform: uppercase;
    letter-spacing: 0.12em;
    line-height: 1.15;
    text-align: center;
  }

  /* Company side */
  .company-top {
    flex: 0 0 230px;
    background: var(--gold);
    display: flex;
    align-items: center;
    justify-content: center;
  }
  .company-top .wordmark { color: var(--paper); font-size: 34px; }
  .company-top .wordmark span { display: block; font-size: 20px; letter-spacing: 0.3em; }
  .company-contact {
    flex: 1;
    background: var(--ink);
    color: var(--paper);
    padding: 24px 0 0 100px;
    font-size: 13.5px;
    line-height: 1.9;
  }
  .contact-row { display: flex; align-items: center; gap: 22px; }
  .contact-item { display: inline-flex; align-items: center; gap: 6px; }
  .contact-item svg { width: 12px; height: 12px; }
  .label { font-weight: 700; }

  /* Staff side */
  .staff-brand {
    flex: 0 0 150px;
    background: var(--paper);
    display: flex;
    align-items: center;
    justify-content: center;
  }
  .staff-brand .wordmark { color: var(--ink); font-size: 30px; }
  .staff-brand .wordmark span { display: block; font-size: 17px; letter-spacing: 0.3em; }
  .person {
    color: var(--paper);
    padding: 0 0 0 70px;
    display: flex;
    flex-direction: column;
    justify-content: center;
    gap: 6px;
    font-size: 14px;
  }
  .person--manager { flex: 0 0 95px; background: var(--gold); }
  .person--director { flex: 1; background: var(--ink); }
  .person-name { font-weight: 700; font-size: 17px; }
  .person-role { font-weight: 400; font-size: 13px; margin-left: 6px; }
  .person-role::before { content: "|"; margin-right: 8px; }
  .person-lines { display: flex; gap: 30px; }
</style>
</head>
<body>

<section class="card card--company" aria-label="Company side of business card">
  <div class="company-top">
    <p class="wordmark">Harcourt<span>Memorials</span></p>
  </div>
  <div class="company-contact">
    <div class="contact-row">
      <span class="contact-item">
        <svg viewBox="0 0 24 24" aria-hidden="true"><path fill="#ebbd2f" d="M6.6 10.8a15.1 15.1 0 0 0 6.6 6.6l2.2-2.2a1 1 0 0 1 1-.25 11.4 11.4 0 0 0 3.6.57 1 1 0 0 1 1 1V20a1 1 0 0 1-1 1A17 17 0 0 1 3 4a1 1 0 0 1 1-1h3.5a1 1 0 0 1 1 1c0 1.25.2 2.45.57 3.57a1 1 0 0 1-.25 1z"/></svg>
        <span><span class="label">P:</span> 02 9561 3048</span>
      </span>
      <span class="contact-item">
        <svg viewBox="0 0 24 24" aria-hidden="true"><circle cx="12" cy="12" r="10" fill="#ebbd2f"/><path d="M2 12h20M12 2c3 3 3 17 0 20M12 2c-3 3-3 17 0 20" stroke="#231f20" stroke-width="1.4" fill="none"/></svg>
        <span>www.harcourtmemorials.com.au</span>
      </span>
    </div>
    <p>Suite 17, 8 Palfrey Lane, West Carlow, Sydney NSW 2156</p>
  </div>
</section>

<section class="card card--staff" aria-label="Staff side of business card">
  <div class="staff-brand">
    <p class="wordmark">Harcourt<span>Memorials</span></p>
  </div>
  <div class="person person--manager">
    <p><span class="person-name">Simon Harcourt</span><span class="person-role">Operations Manager</span></p>
    <p class="person-lines"><span><span class="label">P:</span> 0417293086</span><span><span class="label">E:</span> simon@harcourtmemorials.com.au</span></p>
  </div>
  <div class="person person--director">
    <p><span class="person-name">Lewis Harcourt</span><span class="person-role">Director</span></p>
    <p class="person-lines"><span><span class="label">P:</span> 0491630572</span><span><span class="label">E:</span> lewis@harcourtmemorials.com.au</span></p>
  </div>
</section>

</body>
</html>
```